LB - WESITE NEEDED PAGE: Clean / Modern / Pro & Dynamic

Lantern-Brokers is a new insurance brokerage firm dealing exclusively with companies (BToB) providing the following property: Liabilities Insurance Insurances Automobile Insurance Insurances Construction% 26amp; Engineering Casualty Workmen 's Compensation Health Insurance Marime% 26amp; Transit Credit Insurance Young, Fast, Proactive and Dynamic we call ourselves Lantern-Brokers because we are a "start-up" willing to make a difference in the market, bringing modernity and speed to our industry, still too bureaucratic / procedural / opaque uninitiated. We need something respecting the colors of our orange logtype; blue; white; black; easy to scroll, with simple information on the company; - who we are - our team (with the pictures) - what we do - what we do - contact us, contact us (google map) Luanda (Angola) Small company, just need something flashy / professional / structured / modern.

Target Market(s)

BtoB; Oil and gas companies; French speaking copying established in Angola, all industrials, factories and importers of goods.

Industry/Entity Type

Insurance Broker

Font styles to use
Sans Serif

Colors

Designer to choose colors to be used in the design.

Requirements
Must have
• We need something respecting the colors of our orange logtype; blue; white; black; easy to scroll, with simple information on the company; - who we are - our team (with the pictures) - what we do - what we do - contact us, contact us (google map) Luanda (Angola) Small company, just need something flashy / professional / structured / modern.
Nice to have
• A page format
Should not have
• WE DO NOT WANT A REFER TO OUR LOGO, but a Home Page for our Website with the basics categories ... >> PLEASE CAREFULLY USE THE RIGHT COLOR OF THE LOGOTYPE which are the ones enclosed Orange / Turquoise / Black as per the business card .

```html
<!DOCTYPE html>
<html lang="en">
<head>
<meta charset="utf-8">
<title>Lantern-Brokers — Insurance Brokerage</title>
<link href="https://fonts.googleapis.com/css2?family=Russo+One&family=Jost:wght@400;500;600&display=swap" rel="stylesheet">
<style>
:root{
  --teal:#22706f;
  --teal-light:#58bcc4;
  --orange:#f05a3a;
  --orange-2:#f7814f;
  --blue:#1589e0;
  --blue-2:#21a0f2;
  --ink:#111111;
  --text:#333333;
  --white:#ffffff;
  --panel:#f7f7f7;
  --navy:#18202e;
  --linkedin:#0a73b5;
}
*{box-sizing:border-box;margin:0;padding:0}
html,body{width:1200px;height:3692px;overflow:hidden}
body{font-family:"Jost",sans-serif;color:var(--text);background:var(--white);position:relative}
section,header,footer{position:absolute;left:0;width:1200px}
.heading{font-family:"Russo One",sans-serif;color:var(--ink);letter-spacing:.5px}
.divider{display:flex;align-items:center;gap:10px;justify-content:center}
.divider span{display:block;width:90px;height:2px;background:linear-gradient(90deg,transparent,var(--orange))}
.divider span+i+span{background:linear-gradient(90deg,var(--orange),transparent)}
.divider i{display:block;width:8px;height:8px;border-radius:50%;background:var(--orange)}

/* hero */
.hero{top:0;height:614px;background:var(--teal);overflow:hidden;color:var(--white)}
.brand{position:absolute;left:140px;top:76px;font-weight:600;font-size:18px;color:var(--white)}
.topcontact{position:absolute;right:148px;top:34px;display:flex;gap:22px;font-size:13px}
.topcontact div{display:flex;align-items:center;gap:6px}
.topcontact svg{width:24px;height:24px}
.nav{position:absolute;right:142px;top:78px;display:flex;gap:39px;font-size:13px;font-weight:600;text-transform:uppercase}
.nav a{color:var(--white);text-decoration:none}
.nav a.active{color:var(--orange)}
.hero h1{position:absolute;left:142px;top:266px;font-family:"Russo One",sans-serif;font-size:31px;line-height:44px;font-weight:400}
.hero p{position:absolute;left:142px;top:362px;font-family:"Russo One",sans-serif;font-size:15.5px;line-height:24px}
.dots{position:absolute;display:flex;gap:9px}
.dots i{width:10px;height:10px;border-radius:50%;border:1.5px solid currentColor;display:block}
.dots i.on{background:var(--orange);border-color:var(--orange)}
.hero .dots{left:141px;top:422px;color:var(--white)}
.hero-art{position:absolute;left:617px;top:158px;width:380px;height:456px;background:linear-gradient(200deg,#f4f2ea 0%,#3f7fa8 45%,var(--teal) 80%);opacity:.85;border-radius:50% 50% 0 0}
.hero-clouds{position:absolute;left:0;bottom:0;width:1200px;height:90px;background:linear-gradient(180deg,rgba(88,188,196,0) 0%,var(--teal-light) 100%)}

/* who we are */
.who{top:614px;height:424px}
.mark{position:absolute;left:150px;top:70px;width:270px;height:270px;display:flex;align-items:center;justify-content:center;font-weight:600;font-size:26px;color:var(--ink)}
.who .heading{position:absolute;left:494px;top:74px;font-size:32px}
.who .divider{position:absolute;left:494px;top:124px;justify-content:flex-start}
.who .divider span:first-child{display:none}
.who .lead{position:absolute;left:491px;top:160px;width:560px;font-size:18px;line-height:29px;color:var(--ink)}
.who .body{position:absolute;left:491px;top:230px;width:570px;font-size:14.2px;line-height:25px;color:#444}

/* what we do */
.what{top:1038px;height:534px;background:linear-gradient(120deg,#25262c 0%,#3a3f4b 45%,#2b3140 100%);color:var(--white);text-align:center}
.what .heading{color:var(--white);font-size:32px;margin-top:68px}
.what .divider{margin-top:14px}
.what .intro{width:400px;margin:24px auto 0;font-size:13.5px;line-height:21px}
.services{display:flex;justify-content:center;gap:72px;margin-top:32px}
.service{width:226px}
.service svg{width:90px;height:80px}
.service h3{font-size:13.5px;font-weight:600;letter-spacing:1px;margin-top:10px}
.service p{font-size:13.5px;line-height:22px;margin-top:8px;color:#e8e8e8}
.what .dots{left:574px;top:450px;color:var(--white)}
.what .dots i.on{background:var(--blue-2);border-color:var(--blue-2)}

/* team */
.team{top:1572px;height:590px;text-align:center}
.team .heading{font-size:32px;margin-top:68px}
.team .divider{margin-top:14px}
.team .intro{width:780px;margin:22px auto 0;font-size:13.5px;line-height:23px;color:#333}
.lead-card{position:absolute;left:140px;top:238px;width:178px;height:281px;background:linear-gradient(180deg,var(--orange-2),var(--orange));color:var(--white);box-shadow:0 10px 24px rgba(0,0,0,.18);padding-top:44px}
.lead-card h4{font-family:"Russo One",sans-serif;font-weight:400;font-size:15px}
.lead-card small{display:block;font-size:13px}
.lead-card p{font-size:11.5px;line-height:19px;margin:12px 16px 0;opacity:.9}
.in{display:inline-flex;width:22px;height:22px;border-radius:50%;background:var(--linkedin);color:var(--white);font-size:11px;font-weight:600;align-items:center;justify-content:center}
.lead-card .in{background:var(--white);color:var(--linkedin);margin-top:6px}
.member{position:absolute;top:246px;width:160px;text-align:center}
.member .photo{width:144px;height:144px;margin:0 auto;border-radius:50%;border:5px solid #f1f1f1;box-shadow:0 0 0 1px #e5e5e5;background:linear-gradient(180deg,#d8dde2,#7b8794)}
.member h4{font-family:"Russo One",sans-serif;font-weight:400;font-size:16px;color:var(--ink);margin-top:18px}
.member small{display:block;font-size:13px;color:#444;margin-top:2px}
.member .in{margin-top:14px}

/* why */
.why{top:2162px;height:614px;background:var(--panel);text-align:center}
.why .heading{font-size:32px;margin-top:68px}
.why .divider{margin-top:14px}
.feature{position:absolute;width:283px;height:169px;background:var(--white);box-shadow:0 2px 10px rgba(0,0,0,.06);padding-top:22px}
.feature svg{width:52px;height:52px}
.feature h3{font-size:15px;font-weight:600;letter-spacing:.5px;color:var(--ink);margin-top:10px}
.feature p{font-size:13px;line-height:19px;color:#444;margin:6px 50px 0}
.feature.blue{background:linear-gradient(135deg,var(--blue),var(--blue-2))}
.feature.blue h3,.feature.blue p{color:var(--white)}

/* contact */
.contact{top:2776px;height:594px}
.map{position:absolute;inset:0;background:linear-gradient(135deg,#eef1ec 0%,#e4ebe0 50%,#eef0f2 100%)}
.form-card{position:absolute;left:140px;top:75px;width:464px;height:411px;background:var(--white);box-shadow:0 4px 18px rgba(0,0,0,.12);padding:38px 50px}
.form-card .heading{font-size:32px}
.form-card .divider{justify-content:flex-start;margin-top:12px}
.form-card .divider span:first-child{display:none}
.field{display:flex;align-items:center;gap:12px;height:38px;border:1px solid #dcdcdc;margin-top:14px;padding:0 14px;font-size:13px;color:#555}
.field:first-of-type{margin-top:20px}
.field svg{width:12px;height:12px}
.submit{margin-top:22px;width:142px;height:42px;background:#222;color:var(--white);border:0;font-family:"Jost",sans-serif;font-weight:600;font-size:14px}
.pin-card{position:absolute;left:749px;top:240px;width:292px;height:74px;background:var(--white);box-shadow:0 2px 10px rgba(0,0,0,.15);display:flex;align-items:center;padding:0 24px 0 70px;font-size:13.5px;line-height:20px;color:#333}
.map-pin{position:absolute;left:800px;top:330px}

/* footer */
.footer{top:3370px;height:322px;background:linear-gradient(180deg,#1c2333,var(--navy));color:var(--white);text-align:center}
.footer .divider{margin-top:52px}
.footer .divider span{width:80px}
.fcols{display:flex;justify-content:center;gap:100px;margin-top:44px}
.fcol{width:200px}
.fcol svg{width:44px;height:44px}
.fcol h5{color:var(--orange);font-size:14px;font-weight:600;letter-spacing:.5px;margin-top:10px}
.fcol p{font-size:13.5px;line-height:20px;margin-top:6px}
.copy{position:absolute;left:0;right:0;bottom:0;height:58px;border-top:1px solid rgba(255,255,255,.15);display:flex;align-items:center;justify-content:space-between;padding:0 140px 0 143px;font-size:11.5px}
.social{display:flex;gap:12px}
.social i{width:30px;height:30px;border:1.5px solid var(--white);border-radius:50%;display:block}
</style>
</head>
<body>

<header class="hero">
  <div class="hero-clouds" role="img" aria-label="Soft clouds along the bottom of the banner"></div>
  <div class="hero-art" role="img" aria-label="Illustration of a rocket launching upward with a flame trail"></div>
  <div class="brand">Lantern-Brokers</div>
  <div class="topcontact">
    <div><svg viewBox="0 0 24 24"><circle cx="12" cy="12" r="11" fill="none" stroke="#f05a3a" stroke-width="1.5"/><path d="M8 7l2 0 1 3-1.5 1a7 7 0 0 0 3.5 3.5l1-1.5 3 1v2a1 1 0 0 1-1 1A9 9 0 0 1 7 8a1 1 0 0 1 1-1z" fill="#fff"/></svg>222 410 5530</div>
    <div><svg viewBox="0 0 24 24"><circle cx="12" cy="12" r="11" fill="none" stroke="#f05a3a" stroke-width="1.5"/><rect x="7" y="8.5" width="10" height="7" rx="1" fill="#fff"/><path d="M7 9l5 3.5L17 9" stroke="#22706f" fill="none"/></svg>inquiry@lanternbrokers.com</div>
  </div>
  <nav class="nav">
    <a class="active" href="#">Home</a><a href="#">Who we are</a><a href="#">What we do</a><a href="#">Our team</a><a href="#">Contact us</a>
  </nav>
  <h1>YOUNG, FAST,<br>PROACTIVE &amp; DYNAMIC.</h1>
  <p>WE ARE INSURANCE BROKERAGE FIRM DEALING<br>EXCLUSIVELY WITH COMPANIES</p>
  <div class="dots"><i class="on"></i><i></i><i></i><i></i></div>
</header>

<section class="who">
  <div class="mark">Lantern-Brokers</div>
  <h2 class="heading">WHO WE ARE</h2>
  <div class="divider"><span></span><i></i><span></span></div>
  <p class="lead">Lorem ipsum dolor sit amet, consectetuer adipiscing elit, sedda nonummy nibh euismod tincidunt ut laoreet dolore.</p>
  <p class="body">Lorem ipsum dolor sit amet, enim ad minim veniam, quis nostrud exerci tation ullamcorper suscipit lobortis nisl ut aliquip ex ea commodo consequat. Duis au tem vel eum iriure dolor in hendrerit in vulputate velit esse molestie consequat, vel illum dolore eu feugiat nulla facilisis at vero eros et accumsan et.</p>
</section>

<section class="what" role="img" aria-label="Background photo of a team working at a desk, darkened">
  <h2 class="heading">WHAT WE DO</h2>
  <div class="divider"><span></span><i></i><span></span></div>
  <p class="intro">Lorem ipsum dolor sit amet, enim ad minim veniam, quis nostrud exerci tation ullamcorper suscipit lobortis.</p>
  <div class="services">
    <div class="service">
      <svg viewBox="0 0 90 80" fill="none" stroke-width="3"><circle cx="30" cy="20" r="12" stroke="#f05a3a"/><path d="M10 62v-10a20 20 0 0 1 40 0v10z" stroke="#f05a3a"/><path d="M66 26l16 6v14c0 10-8 16-16 20-8-4-16-10-16-20V32z" stroke="#1589e0"/></svg>
      <h3>LIABILITIES INSURANCE</h3>
      <p>Lorem ipsum dolor sit amet, enim ad minim veniam, quis nostrud exerci tation ullamcorper suscipit lobortis.</p>
    </div>
    <div class="service">
      <svg viewBox="0 0 90 80" fill="none" stroke-width="3"><path d="M30 6l14 5v10c0 8-6 12-14 16-8-4-14-8-14-16V11z" stroke="#f05a3a"/><path d="M12 58l6-14h30l6 14v10H12z" stroke="#f05a3a"/><circle cx="22" cy="68" r="5" stroke="#1589e0"/><circle cx="46" cy="68" r="5" stroke="#1589e0"/><path d="M60 46l12 0 8 12v10H60z" stroke="#1589e0"/></svg>
      <h3>AUTOMOBILE INSURANCE</h3>
      <p>Lorem ipsum dolor sit amet, enim ad minim veniam, quis nostrud exerci tation ullamcorper suscipit lobortis.</p>
    </div>
    <div class="service">
      <svg viewBox="0 0 90 80" fill="none" stroke-width="3"><rect x="34" y="10" width="44" height="34" rx="4" stroke="#1589e0"/><path d="M48 10V4h16v6M56 18v18M47 27h18" stroke="#1589e0"/><path d="M8 60c10 0 14-8 24-8h14a4 4 0 0 1 0 8H34M8 72h40l24-16a4 4 0 0 0-5-6L50 60" stroke="#f05a3a"/></svg>
      <h3>HEALTH INSURANCE</h3>
      <p>Lorem ipsum dolor sit amet, enim ad minim veniam, quis nostrud exerci tation ullamcorper suscipit lobortis.</p>
    </div>
  </div>
  <div class="dots"><i class="on"></i><i></i><i></i></div>
</section>

<section class="team">
  <h2 class="heading">OUR TEAM</h2>
  <div class="divider"><span></span><i></i><span></span></div>
  <p class="intro">Lorem ipsum dolor sit amet, enim ad minim veniam, quis nostrud exerci tation ullamcorper suscipit lobortis nisl ut aliquip ex ea commodo consequat. Duis au tem vel eum iriure dolor in hendrerit in vulputate velit esse molestie consequat,</p>
  <div class="lead-card">
    <h4>ALAN REIS</h4><small>Designation</small>
    <p>Lorem ipsum dolor amet, consectetuer adipiscing diam nonummy euismod tincidunt laoreet dolore magna aliquam...</p>
    <span class="in">in</span>
  </div>
  <div class="member" style="left:333px"><div class="photo" role="img" aria-label="Portrait photo of Tomas"></div><h4>TOMAS</h4><small>Designation</small><span class="in">in</span></div>
  <div class="member" style="left:524px"><div class="photo" role="img" aria-label="Portrait photo of Nuno"></div><h4>NUNO</h4><small>Designation</small><span class="in">in</span></div>
  <div class="member" style="left:713px"><div class="photo" role="img" aria-label="Portrait photo of Pedro" style="background:linear-gradient(180deg,#a9c77a,#5f7d45)"></div><h4>PEDRO</h4><small>Designation</small><span class="in">in</span></div>
  <div class="member" style="left:898px"><div class="photo" role="img" aria-label="Portrait photo of Rafael"></div><h4>RAFAEL</h4><small>Designation</small><span class="in">in</span></div>
</section>

<section class="why">
  <h2 class="heading">WHY CHOOSE US</h2>
  <div class="divider"><span></span><i></i><span></span></div>
  <div class="feature" style="left:140px;top:164px"><svg viewBox="0 0 52 52" fill="none" stroke="#1589e0" stroke-width="2"><circle cx="26" cy="16" r="9"/><path d="M8 48V40c0-8 8-12 18-12s18 4 18 12v8z"/><path d="M23 28l3 10 3-10"/></svg><h3>CERTIFIED EXPERTS</h3><p>Lorem ipsum dolor consectetuer adipiscing elit diam nonummy</p></div>
  <div class="feature blue" style="left:459px;top:164px"><svg viewBox="0 0 52 52" fill="none" stroke="#fff" stroke-width="2"><path d="M10 6h22l8 8v30H10z"/><path d="M16 20h10M16 28h8M16 36h6"/><circle cx="36" cy="34" r="7"/><path d="M41 39l6 6"/></svg><h3>TAX BENEFITS</h3><p>Lorem ipsum dolor consectetuer adipiscing elit diam nonummy</p></div>
  <div class="feature" style="left:777px;top:164px"><svg viewBox="0 0 52 52" fill="none" stroke="#1589e0" stroke-width="2"><rect x="8" y="24" width="8" height="20"/><path d="M16 26l8-12c2-4 6-2 5 2l-2 8h12c3 0 4 3 3 5l-4 12c-1 2-2 3-4 3H16"/><path d="M30 4v4M40 8l-3 3M20 8l3 3"/></svg><h3>WORK SATISFACTION</h3><p>Lorem ipsum dolor consectetuer adipiscing elit diam nonummy</p></div>
  <div class="feature blue" style="left:140px;top:373px"><svg viewBox="0 0 52 52" fill="none" stroke="#fff" stroke-width="2"><circle cx="26" cy="32" r="14"/><path d="M26 32l6-6M26 18v4M14 32h4M34 32h4"/><path d="M26 4v8M14 8l4 6M38 8l-4 6"/></svg><h3>FAST RESPONCE TIME</h3><p>Lorem ipsum dolor consectetuer adipiscing elit diam nonummy</p></div>
  <div class="feature" style="left:459px;top:373px"><svg viewBox="0 0 52 52" fill="none" stroke="#1589e0" stroke-width="2"><rect x="4" y="4" width="16" height="12" rx="2"/><circle cx="34" cy="12" r="6"/><path d="M24 36c0-6 4-10 10-10s10 4 10 10v4H24z"/><circle cx="14" cy="28" r="5"/><path d="M4 48v-4c0-5 4-8 10-8s10 3 10 8v4z"/></svg><h3>FULL SUPPORT</h3><p>Lorem ipsum dolor consectetuer adipiscing elit diam nonummy</p></div>
  <div class="feature blue" style="left:777px;top:373px"><svg viewBox="0 0 52 52" fill="none" stroke="#fff" stroke-width="2"><circle cx="30" cy="16" r="12"/><path d="M30 9v14M26 13h6a2.5 2.5 0 0 1 0 5h-4a2.5 2.5 0 0 0 0 5h6"/><path d="M4 40c8 0 10-6 18-6h8a3 3 0 0 1 0 6h-8M4 48h26l16-10a3 3 0 0 0-4-5l-10 6"/></svg><h3>AFFORDABLE PRICE</h3><p>Lorem ipsum dolor consectetuer adipiscing elit diam nonummy</p></div>
</section>

<section class="contact">
  <div class="map" role="img" aria-label="Street map of the surrounding area showing the office location"></div>
  <div class="form-card">
    <h2 class="heading">LET'S TALK</h2>
    <div class="divider"><span></span><i></i><span></span></div>
    <div class="field"><svg viewBox="0 0 12 12"><circle cx="6" cy="3.5" r="2.5" fill="#f05a3a"/><path d="M1 12a5 5 0 0 1 10 0z" fill="#f05a3a"/></svg>Name</div>
    <div class="field"><svg viewBox="0 0 12 12"><path d="M2 1h2l1 3-1.5 1a6 6 0 0 0 3.5 3.5L8 7l3 1v2a1 1 0 0 1-1 1A9 9 0 0 1 1 2a1 1 0 0 1 1-1z" fill="#f05a3a"/></svg>Phone</div>
    <div class="field"><svg viewBox="0 0 12 12"><rect x="0.5" y="2" width="11" height="8" fill="#f05a3a"/><path d="M1 2.5l5 4 5-4" stroke="#fff" fill="none"/></svg>Email</div>
    <div class="field"><svg viewBox="0 0 12 12" fill="none" stroke="#f05a3a" stroke-width="1.3"><rect x="1" y="2" width="8" height="9"/><path d="M5 8l6-6"/></svg>Message</div>
    <button class="submit">SUBMIT</button>
  </div>
  <div class="pin-card"><span>123 Building Name, Street Name<br>City, State XY 123-456</span></div>
  <svg class="map-pin" width="20" height="26" viewBox="0 0 20 26"><path d="M10 1a8 8 0 0 1 8 8c0 6-8 16-8 16S2 15 2 9a8 8 0 0 1 8-8z" fill="none" stroke="#f05a3a" stroke-width="2.5"/><circle cx="10" cy="9" r="3" fill="#f05a3a"/></svg>
</section>

<footer class="footer">
  <div class="divider"><span></span><i></i><span></span></div>
  <div class="fcols">
    <div class="fcol"><svg viewBox="0 0 44 44" fill="none" stroke="#fff" stroke-width="1.6"><path d="M22 4a12 12 0 0 1 12 12c0 10-12 24-12 24S10 26 10 16A12 12 0 0 1 22 4z"/><circle cx="22" cy="16" r="4"/></svg><h5>ADDRESS</h5><p>123 Building Name, Street Name<br>City, State XY 123-456</p></div>
    <div class="fcol"><svg viewBox="0 0 44 44" fill="none" stroke="#fff" stroke-width="1.6"><rect x="13" y="3" width="18" height="38" rx="3"/><path d="M13 9h18M13 34h18"/><circle cx="22" cy="37.5" r="1.3"/></svg><h5>PHONE</h5><p>222 410 5530</p></div>
    <div class="fcol"><svg viewBox="0 0 44 44" fill="none" stroke="#fff" stroke-width="1.6"><rect x="3" y="9" width="38" height="26"/><path d="M3 9l19 15 19-15M3 35l14-13M41 35L27 22"/></svg><h5>EMAIL</h5><p>inquiry@lanternbrokers.com</p></div>
  </div>
  <div class="copy"><span>Copyright © 2019 Lantern-Brokers. All Rights Reserved.</span><div class="social"><i></i><i></i><i></i></div></div>
</footer>

</body>
</html>
```